Business Card & Letterhead Design

We a financial advice company based in Australia. We provide advice to wealthy farmers.

We are changing our business name FROM Brightvale Financial TO Tallowmere Wealth and we need a new letterhead and double sided business card design

Attached is designs from our previous branding (Brightvale Financial) as it includes all the details we require on the new Tallowmere Wealth business cards and letterhead.

Need extra days to review

```html
<!DOCTYPE html>
<html lang="en">
<head>
<meta charset="utf-8">
<title>Tallowmere Wealth Letterhead</title>
<link href="https://fonts.googleapis.com/css2?family=Open+Sans:wght@400;600;700&display=swap" rel="stylesheet">
<style>
  :root {
    --backdrop: #e6e6e6;
    --paper: #ffffff;
    --ink: #222222;
    --body: #555555;
    --muted: #777777;
    --band: #444444;
  }
  html, body { margin: 0; padding: 0; overflow: hidden; }
  body {
    width: 1040px; height: 1200px;
    background: var(--backdrop);
    font-family: "Open Sans", sans-serif;
    position: relative;
  }
  .letterhead {
    position: absolute; left: 66px; top: 16px;
    width: 790px; height: 1015px;
    background: var(--paper);
    transform: scale(1.15); transform-origin: top left;
    color: var(--ink);
  }
  .letterhead > * { position: absolute; margin: 0; }
  .band-top { right: 0; top: 0; width: 17px; height: 224px; background: var(--band); }
  .band-bottom { left: 0; top: 935px; width: 17px; height: 80px; background: var(--band); }

  .brand { left: 75px; top: 50px; width: 210px; }
  .brand-row { display: flex; align-items: center; gap: 8px; }
  .brand-dot { width: 22px; height: 22px; border: 1.5px solid var(--ink); border-radius: 50%; box-sizing: border-box; }
  .brand-name { font-size: 16px; letter-spacing: 1.2px; text-transform: uppercase; font-weight: 400; }
  .brand-tag { font-size: 6.5px; letter-spacing: 2.4px; text-transform: uppercase; color: var(--muted); margin: 2px 0 0 30px; }

  .sender { right: 82px; top: 32px; text-align: right; font-size: 12.5px; line-height: 18.5px; }
  .sender p { margin: 0; }
  .sender .gap { margin-top: 2px; }
  .sender b { font-weight: 700; }

  .date { left: 75px; top: 233px; font-size: 12px; color: var(--body); }
  .recipient { left: 75px; top: 263px; font-size: 12px; line-height: 15.5px; color: var(--body); }
  .salutation { left: 75px; top: 352px; font-size: 12px; color: var(--body); }
  .body-copy { left: 75px; top: 395px; width: 637px; font-size: 12px; line-height: 23px; color: var(--body); text-align: justify; }
  .body-copy p { margin: 0 0 23px; }
  .closing { left: 75px; top: 740px; font-size: 12px; color: var(--body); }
  .signatory { left: 75px; top: 805px; }
  .signatory-name { font-size: 14.5px; font-weight: 600; color: var(--ink); }
  .signatory-role { font-size: 12px; color: var(--body); margin-top: 3px; }

  .footer-tags { left: 76px; top: 913px; width: 626px; display: flex; justify-content: space-between; font-size: 11px; font-weight: 700; }
  .footer-rule { left: 75px; top: 932px; width: 633px; height: 2px; background: var(--ink); }
  .footer-info { left: 75px; top: 941px; width: 638px; text-align: center; font-size: 12.5px; line-height: 19.5px; }
</style>
</head>
<body>
<div class="letterhead">
  <div class="band-top"></div>
  <div class="band-bottom"></div>

  <div class="brand">
    <div class="brand-row"><span class="brand-dot"></span><span class="brand-name">Tallowmere Wealth</span></div>
    <div class="brand-tag">Strategic Financial Advice</div>
  </div>

  <div class="sender">
    <p>Corwen Holdings Pty Ltd&nbsp; ATF The Ashgrove</p>
    <p>Investment Trust T/AS Brightvale Financial</p>
    <p class="gap"><b>ABN:</b> 52 318 906 417</p>
    <p class="gap">Corporate Authorised Representative</p>
    <p>Of Meridian Advisory Planning Limited</p>
    <p class="gap">Suite 4A, 18 Larkin St Riverbend QLD 4101</p>
    <p>PO Box 5120 Northvale QLD 4101</p>
    <p class="gap"><b>P:</b> (07) 3210 5546 | <b>F:</b> (07) 3210 5547</p>
    <p><b>E:</b> info@brightvalefinancial.com.au</p>
    <p><b>W:</b> www.brightvalefinancial.com.au</p>
  </div>

  <p class="date">Issuing Date: May 5, 2018</p>
  <p class="recipient">Name Of Employee Mr. XYZABC<br>Address of Employee<br>Address Line 2 etc..</p>
  <p class="salutation">Dear Mr.XYZABC</p>

  <div class="body-copy">
    <p>Lorem Ipsum has been the industry's standard dummy text ever since the 1500s, when an unknown printer took a galley of type and scrambled it to make a type specimen book. It has survived not only five centuries, but also the leap into electronic typesetting, remaining essentially unchanged. It was popularised in the 1960s with the release of Letraset sheets containing Lorem Ipsum passages, and more recently with desktop publishing software like Aldus PageMaker including versions of Lorem Ipsum.</p>
    <p>Lorem Ipsum is simply dummy text of the printing and typesetting industry. Lorem Ipsum has been the industry's standard dummy text ever since the 1500s, when an unknown printer took a galley of type and scrambled it to make a type specimen book.</p>
    <p>It has survived not only five centuries, but also the leap into electronic typesetting, remaining essentially unchanged. It was popularised in the 1960s with the release of Letraset sheets containing Lorem IpsumIpsum passages.</p>
  </div>

  <p class="closing">Yours Sincerely</p>
  <div class="signatory">
    <div class="signatory-name">Jonah Whitfield</div>
    <div class="signatory-role">Managing Director</div>
  </div>

  <div class="footer-tags"><span>‘FINANCIAL PEACE OF MIND’</span><span>A REFERRAL BUILT BUSINESS</span></div>
  <div class="footer-rule"></div>
  <div class="footer-info">
    Meridian Advisory Planning Limited &nbsp;| ABN 48 117 530 862<br>
    Australian&nbsp; Financial Services License | License Number 281530<br>
    Principle Address: 410 Harbour Rd. PO Box 1975 Eastbank VIC 3001
  </div>
</div>
</body>
</html>
```